KBT Business Cards

We require business cards for our business. We would like a matte black back to the card, with our logo centred in the middle. The front side of the card is open to design.

Target Market(s)

Clients looking for legal services (professional)

Industry/Entity Type

Legal

Contact Information for Business Card

Doran Kelbrath
Partner
Mobile: 0461 738 524
Email: doran@kbtlaw.co
Website: www.kbtlaw.co
Level 3, 118 Wendmore Street
Sydney NSW 2000

Font styles to use
Other font styles liked:
• Avenir

Colors
f04a50
ffffff
1b1b1b

Requirements
Must have
• Black back with logo included in the centre of the card.
• Our font is Avenir.

```html
<!DOCTYPE html>
<html lang="en">
<head>
<meta charset="utf-8">
<title>KBT Business Cards</title>
<link href="https://fonts.googleapis.com/css2?family=Mulish:wght@400;600;700&display=swap" rel="stylesheet">
<style>
  :root {
    --brand-red: #b91f3f;
    --ink: #1b1b1b;
    --paper: #ffffff;
    --matte: #1c1c1c;
    --matte-emboss: #2a2a2a;
    --rule: #3a3a3a;
    --backdrop: #e6e6e6;
  }
  * { margin: 0; padding: 0; box-sizing: border-box; }
  html, body {
    width: 1200px; height: 912px; overflow: hidden;
    background: var(--backdrop);
    font-family: "Mulish", "Avenir", sans-serif;
  }
  .card {
    position: absolute; left: 250px;
    width: 700px; height: 400px;
    box-shadow: 0 6px 18px rgba(0,0,0,.18);
    overflow: hidden;
  }
  .card--back { top: 36px; background: var(--matte); }
  .card--front { top: 476px; background: var(--paper); }

  /* back */
  .back-mark {
    position: absolute; left: 50%; top: 50%;
    transform: translate(-50%, -50%);
    display: flex; align-items: center; gap: 18px;
  }
  .back-mark__square { width: 46px; height: 46px; background: var(--matte-emboss); }
  .back-mark__name {
    color: var(--matte-emboss); font-weight: 700;
    font-size: 30px; line-height: 1.02; letter-spacing: .5px; text-transform: uppercase;
  }

  /* front */
  .firm-mark {
    position: absolute; right: 44px; top: 42px;
    display: flex; align-items: center; gap: 16px;
  }
  .firm-mark__square { width: 52px; height: 52px; background: var(--brand-red); }
  .firm-mark__name {
    color: var(--ink); font-weight: 700;
    font-size: 24px; line-height: 1.02; text-transform: uppercase;
  }
  .divider {
    position: absolute; left: 40px; right: 40px; top: 150px;
    height: 1px; background: var(--rule);
  }
  .address {
    position: absolute; right: 40px; top: 164px;
    text-align: right; color: var(--ink); font-size: 15px; line-height: 1.35;
  }
  .person { position: absolute; left: 40px; top: 178px; }
  .person__name { color: var(--brand-red); font-weight: 700; font-size: 25px; }
  .person__role { color: var(--ink); font-size: 17px; margin-top: 4px; }
  .person__rule { width: 180px; height: 1px; background: var(--rule); margin: 10px 0 12px; }
  .contact-list { list-style: none; }
  .contact-list li {
    display: flex; align-items: center; gap: 10px;
    color: var(--ink); font-size: 16px; height: 24px;
  }
  .contact-list svg { width: 14px; height: 14px; flex: none; }
  .swoosh { position: absolute; left: 0; top: 0; width: 700px; height: 400px; }
</style>
</head>
<body>

<section class="card card--back" aria-label="Card back">
  <div class="back-mark">
    <span class="back-mark__square"></span>
    <span class="back-mark__name">Kelbrath<br>Brandt<br>Tolley</span>
  </div>
</section>

<section class="card card--front" aria-label="Card front">
  <svg class="swoosh" viewBox="0 0 700 400" aria-hidden="true">
    <path d="M230,345 C430,318 590,262 700,168 L700,186 C590,276 430,330 230,345 Z" fill="var(--ink)"/>
    <path d="M0,400 L0,358 C260,350 520,300 700,198 L700,400 Z" fill="var(--brand-red)"/>
  </svg>

  <div class="firm-mark">
    <span class="firm-mark__square"></span>
    <span class="firm-mark__name">Kelbrath<br>Brandt<br>Tolley</span>
  </div>

  <div class="divider"></div>

  <address class="address" style="font-style:normal">
    Level 3, 118 Wendmore Street<br>Sydney NSW 2000
  </address>

  <div class="person">
    <div class="person__name">Doran Kelbrath</div>
    <div class="person__role">Partner</div>
    <div class="person__rule"></div>
    <ul class="contact-list">
      <li>
        <svg viewBox="0 0 14 14"><path d="M3 1 L5.5 1 L6.5 4 L5 5.2 C5.8 7 7 8.2 8.8 9 L10 7.5 L13 8.5 L13 11 C13 12 12 13 11 13 C5.5 12.5 1.5 8.5 1 3 C1 2 2 1 3 1 Z" fill="var(--brand-red)"/></svg>
        0461 738 524
      </li>
      <li>
        <svg viewBox="0 0 14 14"><rect x="1" y="3" width="12" height="8" rx="1" fill="var(--brand-red)"/><path d="M1.5 3.5 L7 8 L12.5 3.5" stroke="#fff" stroke-width="1.2" fill="none"/></svg>
        doran@kbtlaw.co
      </li>
      <li>
        <svg viewBox="0 0 14 14"><circle cx="7" cy="7" r="6" fill="var(--brand-red)"/><path d="M1 7 H13 M7 1 C4 4 4 10 7 13 M7 1 C10 4 10 10 7 13" stroke="#fff" stroke-width="1" fill="none"/></svg>
        www.kbtlaw.co
      </li>
    </ul>
  </div>
</section>

</body>
</html>
```